Business Card for premium dental clinic

We are a premium dental clinic based in Brasov, Romania with more than 15 year on the market, providing quality dental treatment made by a team of more specialized dentists, working with modern equipment as a solution to beautiful and healthy teeth.

Our current logo for the clinic use 2 square with colors black and gold - dr Ternisu - studio, using family fonts Bodoni, Myriad Pro and Segoe Print.
Depending on the printing we used some gold CMYK background or gold foil picture background or a gold gradient.
We want a business card:
- eye catching business card
- distinguished business card
- premium design
- to keep the color scheme of black and gold
- to attract the customers to spent time reading the information
- modern concept

```html
<!DOCTYPE html>
<html lang="en">
<head>
<meta charset="utf-8">
<title>Dr Ternisu – Business Card</title>
<link rel="stylesheet" href="https://fonts.googleapis.com/css2?family=Roboto+Condensed:wght@400;700&family=Ubuntu+Condensed&family=Roboto:wght@400&display=swap">
<style>
  :root {
    --backdrop: #3b3b3d;
    --card-black: #262628;
    --gold-light: #f6d64a;
    --gold-mid: #e3b11f;
    --gold-deep: #b98a12;
    --paper: #ffffff;
    --ink: #1d1d1f;
    --text-light: #f2f2f2;
  }
  * { box-sizing: border-box; margin: 0; padding: 0; }
  html, body { width: 799px; height: 1200px; overflow: hidden; }
  body {
    background: var(--backdrop);
    font-family: "Ubuntu Condensed", "Roboto Condensed", "Arial Narrow", sans-serif;
    position: relative;
  }
  .card {
    position: absolute;
    left: 80px;
    width: 640px;
    height: 366px;
    background: var(--card-black);
    overflow: hidden;
    box-shadow: 0 14px 30px rgba(0,0,0,.45);
  }
  .card--front { top: 170px; }
  .card--back { top: 664px; }

  .gold-foil {
    background: linear-gradient(135deg, var(--gold-light) 0%, var(--gold-mid) 45%, var(--gold-light) 70%, var(--gold-deep) 100%);
  }

  /* Front */
  .front-gold {
    position: absolute; left: 0; top: 0; width: 50%; height: 100%;
  }
  .name-plate {
    position: absolute;
    background: var(--paper);
    color: var(--ink);
    display: flex; align-items: baseline; justify-content: center;
    white-space: nowrap;
    font-family: "Ubuntu Condensed", "Roboto Condensed", "Arial Narrow", sans-serif;
  }
  .card--front .name-plate {
    left: 30px; top: 100px; width: 290px; height: 96px;
    font-size: 64px; line-height: 96px;
  }
  .name-plate .title { font-size: .5em; margin-right: 4px; }

  .clinic-name {
    position: absolute;
    color: var(--text-light);
    line-height: 1;
    white-space: nowrap;
  }
  .clinic-name .clinic-word { display: block; font-size: 1.3em; margin-bottom: 10px; padding-left: .6em; }
  .clinic-name .clinic-type { display: block; font-family: "Roboto Condensed", "Arial Narrow", sans-serif; font-weight: 700; }
  .card--front .clinic-name { left: 372px; top: 112px; font-size: 40px; }

  /* Back */
  .back-waves { position: absolute; inset: 0; }
  .card--back .name-plate {
    left: 430px; top: 112px; width: 190px; height: 66px;
    font-size: 42px; line-height: 66px;
  }
  .card--back .clinic-name { left: 50px; top: 120px; font-size: 42px; }

  .contact {
    position: absolute; left: 345px; top: 252px;
    font-family: "Roboto", Arial, sans-serif;
    font-size: 14px; color: var(--text-light);
    list-style: none; line-height: 19px;
  }
  .contact li { display: flex; align-items: center; gap: 8px; white-space: nowrap; }
  .contact svg { width: 12px; height: 12px; flex: none; }
  .contact .address { display: block; margin-top: 2px; }
</style>
</head>
<body>

<section class="card card--front" aria-label="Business card front">
  <div class="front-gold gold-foil" role="img" aria-label="Gold foil texture"></div>
  <div class="name-plate"><span class="title">dr.</span>Ternisu</div>
  <div class="clinic-name"><span class="clinic-word">atelier</span><span class="clinic-type">dental clinic</span></div>
</section>

<section class="card card--back" aria-label="Business card back">
  <svg class="back-waves" viewBox="0 0 640 366" role="img" aria-label="Gold foil wave band">
    <defs>
      <linearGradient id="goldWave" x1="0" y1="0" x2="1" y2="1">
        <stop offset="0" stop-color="#f6d64a"/>
        <stop offset=".5" stop-color="#e3b11f"/>
        <stop offset=".75" stop-color="#f6d64a"/>
        <stop offset="1" stop-color="#b98a12"/>
      </linearGradient>
    </defs>
    <path d="M120,0 L640,0 L640,248 C580,258 520,246 460,205 C390,150 300,35 120,0 Z" fill="url(#goldWave)"/>
    <path d="M130,22 C320,40 400,150 478,205 C540,246 600,250 640,240" fill="none" stroke="#262628" stroke-width="12"/>
    <path d="M210,40 C350,70 420,140 470,180 C520,220 580,230 640,222" fill="none" stroke="#262628" stroke-width="7"/>
  </svg>
  <div class="name-plate"><span class="title">dr.</span>Ternisu</div>
  <div class="clinic-name"><span class="clinic-word">atelier</span><span class="clinic-type">dental clinic</span></div>
  <ul class="contact">
    <li><svg viewBox="0 0 12 12" aria-hidden="true"><path d="M2.5 1 L4.5 1 L5 3.5 L3.8 4.4 C4.5 6 6 7.5 7.6 8.2 L8.5 7 L11 7.5 L11 9.5 C11 10.3 10.3 11 9.5 11 C5 11 1 7 1 2.5 C1 1.7 1.7 1 2.5 1 Z" fill="currentColor"/></svg>555-204-7788</li>
    <li><svg viewBox="0 0 12 12" aria-hidden="true"><rect x="0.5" y="2" width="11" height="8" fill="currentColor"/><path d="M0.5 2 L6 6.5 L11.5 2" fill="none" stroke="#262628" stroke-width="1"/></svg>hello@ternisudent.ro</li>
    <li><svg viewBox="0 0 12 12" aria-hidden="true"><circle cx="6" cy="6" r="5" fill="none" stroke="currentColor" stroke-width="1.2"/><ellipse cx="6" cy="6" rx="2.2" ry="5" fill="none" stroke="currentColor" stroke-width="1"/><path d="M1 6 H11" stroke="currentColor" stroke-width="1"/></svg>www.ternisudent.ro</li>
    <li class="address">12 Strada Lungă, Brașov,<br>Brașov County, RO 500035</li>
  </ul>
</section>

</body>
</html>
```